Quiet Harbor, Weekly therapy lessons for the heart of a sister missionary

This is a weekly guided therapy book for female Mormon missionaries. They leave for their missions for 18 months and I am a psychotherapist that is creating a guided workbook to help them through mental health struggles on their mission. I need a good book cover, also preferably something for the spine and back as well. I would like something that gives a soft and safe feeling.

```html
<!DOCTYPE html>
<html lang="en">
<head>
<meta charset="utf-8">
<title>Quiet Harbor – Book Cover</title>
<link href="https://fonts.googleapis.com/css2?family=EB+Garamond:wght@500;600&family=Crimson+Pro:wght@400&display=swap" rel="stylesheet">
<style>
  :root {
    --page: #ffffff;
    --cover: #9a6a3b;
    --glow-core: #fffaf0;
    --glow-warm: #f3c77a;
    --glow-amber: #d49a4e;
    --ink: #ffffff;
    --rule: #d9a766;
  }
  html, body {
    margin: 0;
    padding: 0;
    width: 1200px;
    height: 1200px;
    overflow: hidden;
    background: var(--page);
  }
  .cover {
    position: absolute;
    left: 221px;
    top: 32px;
    width: 758px;
    height: 1138px;
    background: var(--cover);
    overflow: hidden;
  }
  .cover__light {
    position: absolute;
    left: 30px;
    top: 60px;
    width: 700px;
    height: 560px;
    background:
      radial-gradient(circle at 380px 264px, var(--glow-core) 0, rgba(255,246,220,0.9) 14px, rgba(243,199,122,0.55) 50px, rgba(212,154,78,0.25) 130px, rgba(212,154,78,0) 230px),
      radial-gradient(ellipse 340px 200px at 400px 400px, rgba(243,199,122,0.22) 0, rgba(243,199,122,0) 100%);
  }
  .cover__title {
    position: absolute;
    left: 0;
    width: 100%;
    margin: 0;
    font-family: "EB Garamond", "Palatino Linotype", serif;
    font-weight: 600;
    color: var(--ink);
    text-align: center;
    letter-spacing: -4px;
    line-height: 1;
  }
  .cover__title span {
    position: absolute;
    left: 0;
    width: 100%;
    font-size: 206px;
  }
  .cover__title .line-one { top: 518px; }
  .cover__title .line-two { top: 678px; }
  .cover__rule {
    position: absolute;
    left: 241px;
    top: 911px;
    width: 280px;
    height: 2px;
    background: linear-gradient(90deg, rgba(217,167,102,0), var(--rule) 30%, var(--rule) 70%, rgba(217,167,102,0));
  }
  .cover__subtitle {
    position: absolute;
    left: 0;
    top: 930px;
    width: 100%;
    margin: 0;
    font-family: "Crimson Pro", "Minion Pro", serif;
    font-weight: 400;
    font-size: 45px;
    line-height: 59px;
    color: var(--ink);
    text-align: center;
    letter-spacing: -0.5px;
  }
</style>
</head>
<body>
  <main class="cover">
    <div class="cover__light" role="img" aria-label="Radiant golden star burst with a soft halo and scattered sparkles"></div>
    <h1 class="cover__title">
      <span class="line-one">Quiet</span>
      <span class="line-two">Harbor</span>
    </h1>
    <div class="cover__rule"></div>
    <p class="cover__subtitle">Weekly therapy lessons for<br>the heart of a sister missionary</p>
  </main>
</body>
</html>
```